Website Redesign

This is a B2B (Mainly)/B2C website .

Vaporel (our manufacturer) only sells the Sprayer itself. As a result they rarely speak directly to the benefits of a disinfecting chemicals ie. Their marketing is more directed to how quickly the sprayer can cover a given area or how much disinfecting Chemical is saved by spraying instead of the 'spray and wipe method. Also how much labor is saved by spraying.

We will be selling both similar to brindlowash.com

1. Main Selling Point? Infectious disease control and prevention via Electromagnetic Disinfecting Sprayers. Upsell is chemicals used in the sprayer and other products for use in disinfection and cleaning.

Our price point is $1495 so sales generally happen after they speak to our sales team.

End user is in most cases a Business. In some cases an individual as well but 75% business, hospital, School district, Universities.

Redesign is meant to tell a much better story to customer by and presenting a cleaner design. Most important metric is increased conversions.

Number of Pages Required

5+ page

```html
<!DOCTYPE html>
<html lang="en">
<head>
<meta charset="utf-8">
<title>Corvane Group — Disinfecting Sprayers</title>
<link rel="stylesheet" href="https://fonts.googleapis.com/css2?family=Titillium+Web:wght@300;400;600;700&family=Roboto:wght@400;500&display=swap">
<style>
:root{
  --purple:#3a1f9b;
  --red:#e8304b;
  --ink:#333340;
  --muted:#8a8a94;
  --grey-band:#e6e6e8;
  --card-grey:#ececee;
  --white:#ffffff;
  --footer:#1c1c1f;
  --brand-gradient:linear-gradient(90deg,#3b1ea1 0%,#8c2a7a 50%,#ed3148 100%);
}
*{box-sizing:border-box;margin:0;padding:0}
html,body{width:1200px;height:4167px;overflow:hidden}
body{font-family:"Roboto",sans-serif;color:var(--ink);background:var(--white);position:relative}
.section{position:absolute;left:0;width:1200px}
.abs{position:absolute}
.heading{font-family:"Titillium Web",sans-serif;color:var(--purple);font-weight:400}
.center{text-align:center;width:100%}

/* header */
.site-header{top:0;height:76px;background:var(--white)}
.brand{left:144px;top:14px;font-family:"Titillium Web",sans-serif;font-size:37px;font-weight:400;color:var(--red);line-height:44px}
.main-nav{right:146px;top:30px;display:flex;gap:32px;font-family:"Roboto",sans-serif;font-size:13px;color:#555}
.main-nav a{color:#555;text-decoration:none}
.main-nav a.active{color:var(--purple)}

/* hero */
.hero{top:76px;height:538px;background:var(--brand-gradient)}
.hero-product{left:145px;top:80px;width:380px;height:458px;border-radius:40px 40px 0 0;background:radial-gradient(ellipse at 45% 40%,#b9b9c2 0%,#55555f 45%,rgba(40,30,80,0.2) 75%)}
.hero-title{right:146px;top:145px;text-align:right;font-family:"Titillium Web",sans-serif;font-weight:600;font-size:48px;line-height:60px;color:var(--white)}
.hero-text{right:146px;top:270px;width:520px;text-align:right;font-size:13.5px;line-height:24px;color:var(--white)}
.btn-outline{display:block;border:2px solid var(--white);color:var(--white);border-radius:24px;font-family:"Titillium Web",sans-serif;font-weight:600;font-size:15px;text-align:center}
.hero-btn{left:910px;top:333px;width:144px;height:47px;line-height:43px}
.arrow{width:30px;height:40px}
.hero .arrow-left{left:50px;top:248px}
.hero .arrow-right{left:1120px;top:248px}

/* welcome */
.welcome{top:614px;height:478px}
.welcome-title{left:144px;top:86px;font-size:42px;font-weight:600}
.welcome-text{left:144px;top:154px;width:540px;font-size:13px;line-height:25.8px;color:#444}
.btn-red{display:block;background:var(--red);color:var(--white);border-radius:24px;font-family:"Titillium Web",sans-serif;font-weight:600;font-size:15px;text-align:center}
.welcome-btn{left:144px;top:330px;width:144px;height:44px;line-height:44px}
.welcome-photo{left:736px;top:78px;width:318px;height:318px;border-radius:50%;background:linear-gradient(135deg,#c9b79c 0%,#7f6a64 40%,#2e3e78 70%,#b8a89a 100%)}

/* products */
.products{top:1092px;height:648px;background:var(--grey-band)}
.products-title{top:68px;font-size:42px;font-weight:600}
.product-card{top:140px;width:298px;height:409px;background:var(--white);box-shadow:0 8px 18px rgba(0,0,0,0.12)}
.product-image{position:absolute;left:49px;top:40px;width:200px;height:270px;background:radial-gradient(ellipse at 50% 45%,#6c6c74 0%,#2c2c32 55%,#ffffff 80%)}
.product-name{position:absolute;left:0;width:100%;top:350px;text-align:center;font-family:"Titillium Web",sans-serif;font-size:19px;color:#2b2b33}

/* checklist */
.checklist-section{top:1740px;height:446px}
.sub-title{font-size:28px;font-weight:300}
.checklist-title{left:144px;top:70px}
.checklist{left:144px;top:124px;list-style:none;font-size:12.5px;color:#333}
.checklist li{height:32px;display:flex;align-items:flex-start;gap:10px}
.checklist svg{flex:none;margin-top:2px}
.mask-photo{left:655px;top:79px;width:399px;height:284px;background:linear-gradient(90deg,#cdb9ac 0%,#a2877a 55%,#bfa79b 100%)}

/* team */
.team{top:2186px;height:469px;background:var(--grey-band)}
.team-photo{left:144px;top:79px;width:399px;height:311px;background:linear-gradient(135deg,#cfc3b0 0%,#5c6470 45%,#d8c9b2 100%)}
.team-title{left:572px;top:76px}
.arrow-list{left:572px;top:126px;width:482px;list-style:none;font-size:12px;line-height:19px;color:#333}
.arrow-list li{display:flex;gap:10px;margin-bottom:19px}
.arrow-list svg{flex:none;margin-top:5px}

/* blog */
.blog{top:2655px;height:730px}
.blog-title{top:68px;font-size:42px;font-weight:600}
.blog-card{top:145px;width:427px;height:495px;background:var(--card-grey)}
.blog-image{height:321px}
.blog-card.kids .blog-image{background:linear-gradient(160deg,#5aa4c6 0%,#b58a6e 45%,#303a5a 100%)}
.blog-card.clinic .blog-image{background:linear-gradient(160deg,#d7d6d0 0%,#2e7fbf 45%,#d66a2a 100%)}
.blog-heading{padding:28px 30px 0;font-family:"Titillium Web",sans-serif;font-size:18.5px;line-height:25px;color:#333}
.blog-excerpt{padding:12px 30px 0;font-size:11px;line-height:19px;color:#8a8a94}
.blog .arrow-left{left:46px;top:378px}
.blog .arrow-right{left:1122px;top:378px}

/* call to action */
.cta{top:3385px;height:304px;background:var(--brand-gradient)}
.cta-text{top:65px;font-family:"Titillium Web",sans-serif;font-weight:300;font-size:27px;line-height:46px;color:var(--white)}
.price-btn{left:504px;top:158px;width:192px;height:80px;border-radius:40px;font-size:38px;font-weight:700;line-height:74px}

/* industries */
.industries{top:3689px;height:363px}
.industries-title{top:70px;font-size:42px;font-weight:600}
.industry{top:162px;width:220px;text-align:center}
.industry svg{display:block;margin:0 auto}
.industry span{display:block;margin-top:16px;font-family:"Titillium Web",sans-serif;font-size:24px;color:#2b2b33}

/* footer */
.site-footer{top:4052px;height:115px;background:var(--footer);color:#c9c9cf}
.footer-links{left:144px;top:34px;font-size:11px}
.footer-links a{color:#c9c9cf;text-decoration:none}
.footer-links i{font-style:normal;margin:0 9px}
.copyright{left:144px;top:67px;font-size:11px}
.social{left:942px;top:45px;display:flex;gap:22px}
.social span{width:20px;height:20px;border-radius:50%;background:#c9c9cf}
.footer-mark{right:12px;top:96px;font-size:10px;color:#fff}
</style>
</head>
<body>

<header class="section site-header">
  <div class="abs brand">Corvane Group</div>
  <nav class="abs main-nav">
    <a class="active" href="#">HOME</a>
    <a href="#">ABOUT US</a>
    <a href="#">INDUSTRIES</a>
    <a href="#">NEWS</a>
    <a href="#">CONTACT US</a>
  </nav>
</header>

<section class="section hero">
  <div class="abs hero-product" role="img" aria-label="Handheld electrostatic disinfecting sprayer"></div>
  <svg class="abs arrow arrow-left" viewBox="0 0 30 40"><polyline points="20,8 8,20 20,32" fill="none" stroke="#fff" stroke-width="4"/></svg>
  <svg class="abs arrow arrow-right" viewBox="0 0 30 40"><polyline points="10,8 22,20 10,32" fill="none" stroke="#fff" stroke-width="4"/></svg>
  <h1 class="abs hero-title">Vestibulum primis<br>faucibus luctus</h1>
  <p class="abs hero-text">Donec vestibulum odio sem, ac laoreet massa ullamcorper id. Donec molestie nisi et tellus hendrerit vehicula. Nunc eu ligula sed quam.</p>
  <a class="abs btn-outline hero-btn" href="#">LEARN MORE</a>
</section>

<section class="section welcome">
  <h2 class="abs heading welcome-title">Welcome to Corvane Group</h2>
  <p class="abs welcome-text">Fusce porta arcu mi, aliquet dictum nulla interdum quis. Donec quis ex semper, consequat ligula at, efficitur lacus. Phasellus elementum lacinia quam non pellentesque. Aliquam malesuada eros sit amet turpis scelerisque maximus. Maecenas lobortis iaculis efficitur. Nulla facilisi. Vestibulum pharetra diam ex, in posuere purus efficitur ac. Mauris placerat eros lorem, vel egestas mi mattis eget. Donec a nisl vel ante tristique mollis nec quis est. Praesent accumsan nunc a condimentum volutpat. Sed quis metus nibh.</p>
  <a class="abs btn-red welcome-btn" href="#">LEARN MORE</a>
  <div class="abs welcome-photo" role="img" aria-label="Staff member spraying a classroom with a disinfecting sprayer"></div>
</section>

<section class="section products">
  <h2 class="abs heading center products-title">Our Products</h2>
  <div class="abs product-card" style="left:144px">
    <div class="product-image" role="img" aria-label="Handheld sprayer"></div>
    <div class="product-name">Mauris pulvinar volutpat</div>
  </div>
  <div class="abs product-card" style="left:451px">
    <div class="product-image" role="img" aria-label="Backpack sprayer"></div>
    <div class="product-name">Integer sapien felis</div>
  </div>
  <div class="abs product-card" style="left:758px">
    <div class="product-image" role="img" aria-label="Cart-mounted sprayer"></div>
    <div class="product-name">Pellentesque magna</div>
  </div>
</section>

<section class="section checklist-section">
  <h3 class="abs heading sub-title checklist-title">Fusce aliquet efficitur</h3>
  <ul class="abs checklist">
    <li><svg width="11" height="11" viewBox="0 0 12 12"><circle cx="6" cy="6" r="6" fill="#e8304b"/><polyline points="3.2,6.2 5.2,8 8.8,4" fill="none" stroke="#fff" stroke-width="1.6"/></svg>Fusce porta arcu mi, aliquet dictum nulla interdum quis.</li>
    <li><svg width="11" height="11" viewBox="0 0 12 12"><circle cx="6" cy="6" r="6" fill="#e8304b"/><polyline points="3.2,6.2 5.2,8 8.8,4" fill="none" stroke="#fff" stroke-width="1.6"/></svg>Donec quis ex semper, consequat ligula.</li>
    <li><svg width="11" height="11" viewBox="0 0 12 12"><circle cx="6" cy="6" r="6" fill="#e8304b"/><polyline points="3.2,6.2 5.2,8 8.8,4" fill="none" stroke="#fff" stroke-width="1.6"/></svg>Phasellus elementum lacinia quam non pellentesque.</li>
    <li><svg width="11" height="11" viewBox="0 0 12 12"><circle cx="6" cy="6" r="6" fill="#e8304b"/><polyline points="3.2,6.2 5.2,8 8.8,4" fill="none" stroke="#fff" stroke-width="1.6"/></svg>Aliquam malesuada eros sit amet turpis scelerisque maximus.</li>
    <li><svg width="11" height="11" viewBox="0 0 12 12"><circle cx="6" cy="6" r="6" fill="#e8304b"/><polyline points="3.2,6.2 5.2,8 8.8,4" fill="none" stroke="#fff" stroke-width="1.6"/></svg>Maecenas lobortis iaculis efficitur.</li>
    <li><svg width="11" height="11" viewBox="0 0 12 12"><circle cx="6" cy="6" r="6" fill="#e8304b"/><polyline points="3.2,6.2 5.2,8 8.8,4" fill="none" stroke="#fff" stroke-width="1.6"/></svg>Vestibulum pharetra diam ex, in posuere purus efficitur.</li>
    <li><svg width="11" height="11" viewBox="0 0 12 12"><circle cx="6" cy="6" r="6" fill="#e8304b"/><polyline points="3.2,6.2 5.2,8 8.8,4" fill="none" stroke="#fff" stroke-width="1.6"/></svg>Mauris placerat eros lorem, vel egestas mi mattis eget.</li>
    <li><svg width="11" height="11" viewBox="0 0 12 12"><circle cx="6" cy="6" r="6" fill="#e8304b"/><polyline points="3.2,6.2 5.2,8 8.8,4" fill="none" stroke="#fff" stroke-width="1.6"/></svg>Donec a nisl vel ante tristique mollis nec quis est.</li>
  </ul>
  <div class="abs mask-photo" role="img" aria-label="Close-up of a person wearing a surgical mask"></div>
</section>

<section class="section team">
  <div class="abs team-photo" role="img" aria-label="Business team meeting around a conference table"></div>
  <h3 class="abs heading sub-title team-title">Mauris pulvinar volutpat</h3>
  <ul class="abs arrow-list">
    <li><svg width="7" height="9" viewBox="0 0 7 9"><polyline points="1.5,1 5.5,4.5 1.5,8" fill="none" stroke="#e8304b" stroke-width="2"/></svg><span>Pellentesque magna orci, placerat at nisl at, porta ultrices turpis. Fusce in eros non orci posuere viverra ut a lectus. In mattis, lorem sit amet consequat placerat, augue nulla mollis turpis, vitae egestas est tellus in nulla. Vestibulum convallis rutrum tincidunt. Aenean sit amet suscipit leo.</span></li>
    <li><svg width="7" height="9" viewBox="0 0 7 9"><polyline points="1.5,1 5.5,4.5 1.5,8" fill="none" stroke="#e8304b" stroke-width="2"/></svg><span>Pellentesque accumsan ut metus sed elementum. Integer ac ante neque. Vestibulum a eleifend sapien, at consectetur risus. Nulla finibus lacinia dolor, semper dictum leo eleifend non. Etiam non nulla non turpis pharetra tincidunt sed ut lorem.</span></li>
    <li><svg width="7" height="9" viewBox="0 0 7 9"><polyline points="1.5,1 5.5,4.5 1.5,8" fill="none" stroke="#e8304b" stroke-width="2"/></svg><span>Etiam bibendum eros at velit consectetur commodo.</span></li>
    <li><svg width="7" height="9" viewBox="0 0 7 9"><polyline points="1.5,1 5.5,4.5 1.5,8" fill="none" stroke="#e8304b" stroke-width="2"/></svg><span>Praesent sollicitudin, justo quis faucibus dapibus, massa erat porta purus, eu faucibus felis leo eget lacus. Cras dapibus augue ac hendrerit interdum.</span></li>
  </ul>
</section>

<section class="section blog">
  <h2 class="abs heading center blog-title">Blog</h2>
  <svg class="abs arrow arrow-left" viewBox="0 0 30 40"><polyline points="20,8 8,20 20,32" fill="none" stroke="#9a9aa2" stroke-width="3"/></svg>
  <svg class="abs arrow arrow-right" viewBox="0 0 30 40"><polyline points="10,8 22,20 10,32" fill="none" stroke="#9a9aa2" stroke-width="3"/></svg>
  <article class="abs blog-card kids" style="left:144px">
    <div class="blog-image" role="img" aria-label="Students working together at classroom desks"></div>
    <h4 class="blog-heading">Fusce vitae lectus sit amet pulvinar maximus placerat.</h4>
    <p class="blog-excerpt">Phasellus nisl est, condimentum vitae faucibus in, sollicitudin vel metus. Nunc sit amet consequat risus. Curabitur ac elit leo. In eleifend dui tellus, in scelerisque elit porttitor.</p>
  </article>
  <article class="abs blog-card clinic" style="left:627px">
    <div class="blog-image" role="img" aria-label="Nurse taking notes with a patient in a clinic"></div>
    <h4 class="blog-heading">Aenean sed quam non sapien faucibus con-sequat vitae sit amet.</h4>
    <p class="blog-excerpt">Phasellus nisl est, condimentum vitae faucibus in, sollicitudin vel metus. Nunc sit amet consequat risus. Curabitur ac elit leo. In eleifend dui tellus, in scelerisque elit porttitor.</p>
  </article>
</section>

<section class="section cta">
  <p class="abs center cta-text">Integer tellus tempus sit amet nisi rhoncus feugiat risus. Proin efficitur<br>sem nec imperdiet rhoncus enim neque tempor.</p>
  <a class="abs btn-outline price-btn" href="#">$1495</a>
</section>

<section class="section industries">
  <h2 class="abs heading center industries-title">Industries</h2>
  <div class="abs industry" style="left:131px">
    <svg width="86" height="80" viewBox="0 0 86 80" fill="none" stroke="#3a1f9b" stroke-width="2.5"><rect x="22" y="8" width="40" height="70"/><rect x="6" y="34" width="16" height="44"/><rect x="62" y="28" width="18" height="50"/><g stroke="#e8304b"><rect x="30" y="18" width="6" height="8"/><rect x="46" y="18" width="6" height="8"/><rect x="30" y="36" width="6" height="8"/><rect x="46" y="36" width="6" height="8"/><rect x="37" y="60" width="10" height="18"/></g></svg>
    <span>Business</span>
  </div>
  <div class="abs industry" style="left:369px">
    <svg width="86" height="80" viewBox="0 0 86 80" fill="none" stroke="#3a1f9b" stroke-width="2.5"><rect x="12" y="26" width="62" height="52"/><rect x="30" y="6" width="26" height="20"/><g stroke="#e8304b"><line x1="43" y1="10" x2="43" y2="22"/><line x1="37" y1="16" x2="49" y2="16"/><rect x="20" y="36" width="8" height="10"/><rect x="39" y="36" width="8" height="10"/><rect x="58" y="36" width="8" height="10"/><rect x="36" y="58" width="14" height="20"/></g></svg>
    <span>Hospital</span>
  </div>
  <div class="abs industry" style="left:608px">
    <svg width="86" height="80" viewBox="0 0 86 80" fill="none" stroke="#3a1f9b" stroke-width="2.5"><polyline points="6,40 43,18 80,40"/><rect x="12" y="40" width="62" height="38"/><line x1="43" y1="18" x2="43" y2="4"/><g stroke="#e8304b"><polyline points="43,4 52,7 43,10"/><circle cx="43" cy="32" r="5"/><rect x="20" y="48" width="8" height="9"/><rect x="58" y="48" width="8" height="9"/><rect x="37" y="58" width="12" height="20"/></g></svg>
    <span>School District</span>
  </div>
  <div class="abs industry" style="left:847px">
    <svg width="86" height="80" viewBox="0 0 86 80" fill="none" stroke="#3a1f9b" stroke-width="2.5"><rect x="26" y="20" width="34" height="58"/><rect x="8" y="40" width="18" height="38"/><rect x="60" y="40" width="18" height="38"/><polyline points="26,20 43,8 60,20"/><g stroke="#e8304b"><rect x="34" y="30" width="6" height="8"/><rect x="46" y="30" width="6" height="8"/><rect x="14" y="50" width="6" height="8"/><rect x="66" y="50" width="6" height="8"/><rect x="37" y="60" width="12" height="18"/></g></svg>
    <span>Universities</span>
  </div>
</section>

<footer class="section site-footer">
  <div class="abs footer-links"><a href="#">Home</a><i>|</i><a href="#">About Us</a><i>|</i><a href="#">Industries</a><i>|</i><a href="#">News</a><i>|</i><a href="#">Contact Us</a></div>
  <div class="abs copyright">Copyright © 2020 &nbsp;Corvane Group. &nbsp;All rights reserved.</div>
  <div class="abs social" aria-label="Social links"><span></span><span></span><span></span></div>
</footer>

</body>
</html>
```